New, modern business card for growing audiology practice

We need a new business card for our audiology practice. Our logo and website have recently changed (more modern) and we want our business cards to reflect this change.
We conduct hearing tests, perform earwax removals, and fit & dispense hearing aids to our patients. We are a family owned practice in which the owner is the one who works directly with the patient. I have attached logos in various formats to use, as well as two ideas I found on this website; as well as a scanned copy of our current logo. Good luck!

Industry/Entity Type

Business

Contact Information for Business Card

Company name: Tolvera Hearing Center
Provider name: Peter Wolstenby, Au.D. F/NSB
Phone number: (440) 683-5127
Address: 837 W. Lindell Ave. Marlow Falls, OH 44187
email: tolverahearing@postvane.com
website: tolverahearing.com

Colors
000000
aaaaaa
dbdbdb
cacaca
9bcb3c
afd23c
cadf82
b1b1b1

Requirements
Must have
• My card must include information in the "details" section. In the attached images, I found a few that I liked and I would like to model after - "brisky bouncin'" and "Sound Method Center".
• Must be horizontal.
• Must include logos provided. I uploaded them in various file formats and various ways.
• Must match logo font, if possible, if not, please get as close as you can.
Nice to have
• I really like the idea of having a color on one side with just the logo and company name and the contact information and provider name on the other side. I also really like the idea of having the main color dominating on the logo/company side with accent of that same color on the contact side of the card.
Should not have
• Must not be vertical.

```html
<!DOCTYPE html>
<html lang="en">
<head>
<meta charset="utf-8">
<title>Tolvera Hearing Center – Business Card</title>
<link href="https://fonts.googleapis.com/css2?family=Roboto:wght@400;500;700&display=swap" rel="stylesheet">
<style>
  :root{
    --stage:#2b2c2e;
    --card-dark:#1c1e20;
    --card-light:#f3f3f2;
    --green:#76a33e;
    --ink:#111111;
    --ink-soft:#4a4a4a;
    --white:#ffffff;
  }
  *{margin:0;padding:0;box-sizing:border-box}
  html,body{width:1200px;height:960px;overflow:hidden;background:var(--stage)}
  body{position:relative;font-family:'Roboto',Arial,sans-serif}

  .card{position:absolute;left:320px;width:600px;border-radius:20px;overflow:hidden}

  .card-back{top:100px;height:355px;background:var(--card-dark);
    box-shadow:0 8px 0 -2px #18191b,0 12px 24px rgba(0,0,0,.5)}
  .back-mark{position:absolute;left:0;right:0;top:150px;
    display:flex;justify-content:center;align-items:center;gap:14px}
  .back-mark .dot{width:22px;height:22px;border-radius:50%;background:var(--green)}
  .back-mark .brand{font-weight:500;font-size:30px;color:var(--green);letter-spacing:1px;text-transform:uppercase}
  .back-url{position:absolute;left:0;right:0;top:302px;text-align:center;
    color:var(--white);font-size:14px;letter-spacing:4px}

  .card-front{top:493px;height:342px;background:var(--card-light);
    box-shadow:0 10px 24px rgba(0,0,0,.5)}
  .green-panel{position:absolute;left:0;top:0}
  .front-brand{position:absolute;right:32px;top:36px;display:flex;align-items:center;gap:10px}
  .front-brand .dot{width:14px;height:14px;border-radius:50%;background:var(--green)}
  .front-brand .brand{font-weight:400;font-size:22px;color:var(--ink);text-transform:uppercase;letter-spacing:.3px}

  .details{position:absolute;right:30px;top:152px;text-align:right}
  .name{font-weight:700;font-size:21px;color:var(--green);text-transform:uppercase;line-height:24px}
  .credential{font-weight:700;font-size:14px;color:var(--ink);letter-spacing:.5px;margin-top:3px}
  .address{font-size:14px;color:var(--ink-soft);line-height:18px;margin-top:12px}
  .contact-list{list-style:none;margin-top:10px}
  .contact-list li{font-size:14px;color:var(--ink-soft);line-height:19px;display:flex;justify-content:flex-end;align-items:center;gap:12px}
  .contact-list svg{width:14px;height:14px;fill:var(--green)}
</style>
</head>
<body>

<section class="card card-back">
  <div class="back-mark"><span class="dot"></span><span class="brand">Tolvera Hearing Center</span></div>
  <p class="back-url">www.tolverahearing.com</p>
</section>

<section class="card card-front">
  <svg class="green-panel" width="240" height="342" viewBox="0 0 240 342" aria-hidden="true">
    <path d="M0 0 H100 C190 30 230 110 200 190 C175 255 120 300 90 342 H0 Z" fill="var(--green)"/>
  </svg>

  <div class="front-brand"><span class="dot"></span><span class="brand">Tolvera Hearing Center</span></div>

  <div class="details">
    <h1 class="name">Peter Wolstenby</h1>
    <p class="credential">AU.D. F/NSB</p>
    <p class="address">837 W. Lindell Ave.<br>Marlow Falls, OH 44187</p>
    <ul class="contact-list">
      <li>(440) 683-5127
        <svg viewBox="0 0 24 24"><path d="M6.6 10.8a15.1 15.1 0 006.6 6.6l2.2-2.2c.3-.3.7-.4 1-.2 1.1.4 2.3.6 3.6.6.6 0 1 .4 1 1V20c0 .6-.4 1-1 1A17 17 0 013 4c0-.6.4-1 1-1h3.5c.6 0 1 .4 1 1 0 1.3.2 2.5.6 3.6.1.3 0 .7-.2 1z"/></svg></li>
      <li>tolverahearing@postvane.com
        <svg viewBox="0 0 24 24"><path d="M2 5h20v14H2z"/><path d="M3 6.5l9 7 9-7" stroke="#f3f3f2" stroke-width="1.6" fill="none"/></svg></li>
      <li>tolverahearing.com
        <svg viewBox="0 0 24 24"><circle cx="12" cy="12" r="10"/><path d="M2 12h20M12 2c3 3 3 17 0 20M12 2c-3 3-3 17 0 20" stroke="#f3f3f2" stroke-width="1.4" fill="none"/></svg></li>
    </ul>
  </div>
</section>

</body>
</html>
```